Harborline Auto LLC

Car Dealer Customer Service
Address: 2874 Cresthaven Road, Shelbyville, TN 37162
web: www.harborlineautoxq.net
email: harborlineautoxq@mailnest.example
Phone: (931) 555-0148
Phone: (629) 555-0173

```html
<!DOCTYPE html>
<html lang="en">
<head>
<meta charset="utf-8">
<title>Harborline Auto – Business Card</title>
<link href="https://fonts.googleapis.com/css2?family=Montserrat:wght@400;500;800&display=swap" rel="stylesheet">
<style>
  :root{
    --page:#e6e7e9;
    --brand-blue:#1f7bb0;
    --brand-blue-light:#2a95cf;
    --brand-gold:#eab245;
    --ink:#1b1b1b;
    --paper:#ffffff;
  }
  *{box-sizing:border-box;margin:0;padding:0}
  html,body{width:1200px;height:887px;overflow:hidden;background:var(--page)}
  body{font-family:"Montserrat",sans-serif;position:relative}
  .card{
    position:absolute;left:250px;width:700px;height:400px;border-radius:34px;
    box-shadow:0 10px 28px rgba(0,0,0,.18);overflow:hidden;
  }
  .card--front{top:36px;background:var(--brand-blue)}
  .card--back{top:460px;background:var(--paper)}

  .front__mark{
    position:absolute;left:50%;top:70px;transform:translateX(-50%);
    width:150px;height:150px;border-radius:50%;background:var(--brand-blue-light);
    border:10px solid var(--paper);
  }
  .front__name{
    position:absolute;left:0;right:0;top:250px;text-align:center;
    font-weight:800;font-size:50px;letter-spacing:1px;color:var(--paper);text-transform:uppercase;
  }

  .back__info{position:absolute;left:56px;top:62px;width:380px}
  .back__name{font-weight:800;font-size:34px;color:var(--brand-blue);text-transform:uppercase;letter-spacing:.5px;margin-bottom:20px}
  .back__role,.back__address{font-size:17px;color:var(--ink);line-height:1.45}
  .back__address{margin-bottom:24px}
  .contact{list-style:none}
  .contact li{display:flex;align-items:center;gap:14px;font-size:17px;color:var(--ink);line-height:1.75;white-space:nowrap}
  .contact svg{width:18px;height:18px;flex:none;fill:var(--brand-blue)}

  .back__mark{
    position:absolute;right:70px;top:78px;width:220px;height:220px;border-radius:50%;
    background:var(--brand-blue-light);
  }
  .back__mark-name{
    position:absolute;right:50px;top:312px;width:260px;text-align:center;
    font-weight:800;font-size:22px;color:var(--brand-blue);text-transform:uppercase;
  }
</style>
</head>
<body>
  <section class="card card--front" aria-label="Business card front">
    <div class="front__mark"></div>
    <h1 class="front__name">Harborline Auto</h1>
  </section>

  <section class="card card--back" aria-label="Business card back">
    <div class="back__info">
      <h2 class="back__name">Harborline Auto</h2>
      <p class="back__role">Car Dealer Customer Service</p>
      <p class="back__address">2874 Cresthaven Road<br>Shelbyville, TN 37162</p>
      <ul class="contact">
        <li><svg viewBox="0 0 24 24" aria-hidden="true"><path d="M6.6 10.8a15.1 15.1 0 0 0 6.6 6.6l2.2-2.2a1 1 0 0 1 1-.25 11.4 11.4 0 0 0 3.6.57 1 1 0 0 1 1 1V20a1 1 0 0 1-1 1A17 17 0 0 1 3 4a1 1 0 0 1 1-1h3.5a1 1 0 0 1 1 1c0 1.25.2 2.45.57 3.57a1 1 0 0 1-.25 1z"/></svg>(931) 555-0148</li>
        <li><svg viewBox="0 0 24 24" aria-hidden="true"><path d="M12 6c-4 0-8 1.5-9.5 3.5L4 13l4-1.2V9.5c1.2-.4 2.6-.6 4-.6s2.8.2 4 .6v2.3l4 1.2 1.5-3.5C20 7.5 16 6 12 6zM6 14h12l1 6H5z"/></svg>(629) 555-0173</li>
        <li><svg viewBox="0 0 24 24" aria-hidden="true"><path d="M2 5h20v14H2zm2 2v.5l8 5.5 8-5.5V7z"/></svg>harborlineautoxq@mailnest.example</li>
        <li><svg viewBox="0 0 24 24" aria-hidden="true"><path d="M12 2a10 10 0 1 0 0 20 10 10 0 0 0 0-20zm6.9 6h-3a15 15 0 0 0-1.3-3.9A8 8 0 0 1 18.9 8zM12 4c.8 1.1 1.5 2.5 1.9 4h-3.8c.4-1.5 1.1-2.9 1.9-4zM4.3 14a8 8 0 0 1 0-4h3.4a16 16 0 0 0 0 4zm.8 2h3a15 15 0 0 0 1.3 3.9A8 8 0 0 1 5.1 16zm3-8h-3a8 8 0 0 1 4.3-3.9A15 15 0 0 0 8.1 8zM12 20c-.8-1.1-1.5-2.5-1.9-4h3.8c-.4 1.5-1.1 2.9-1.9 4zm2.3-6H9.7a14 14 0 0 1 0-4h4.6a14 14 0 0 1 0 4zm.3 5.9a15 15 0 0 0 1.3-3.9h3a8 8 0 0 1-4.3 3.9zm1.7-5.9a16 16 0 0 0 0-4h3.4a8 8 0 0 1 0 4z"/></svg>www.harborlineautoxq.net</li>
      </ul>
    </div>
    <div class="back__mark"></div>
    <p class="back__mark-name">Harborline Auto</p>
  </section>
</body>
</html>
```